Calvanto Group Real Estate Company business cards

New business card design, we are generally happy with the basic layout of the existing front of business card, (feel free to change) but require a head shot photo on the back side.

http://www.calvanto.com.au/

Attached logos, and existing business card

------------------------------

Target Market(s)

Real estate

Industry/Entity Type

Real Estate

Contact Information for Business Card

Standard size double sided

Font styles to use
Other font styles liked:
• Futura

Requirements
Must have
• Photo head shot on the back side
Nice to have
• yes
Should not have
• No

```html
<!DOCTYPE html>
<html lang="en">
<head>
<meta charset="utf-8">
<title>Calvanto Group – Business Cards</title>
<link href="https://fonts.googleapis.com/css2?family=Jost:wght@400;500;700&family=Roboto:wght@400;500&display=swap" rel="stylesheet">
<style>
  :root{
    --bg:#e4e4e6;
    --purple-dark:#2a1247;
    --purple:#3f1f6b;
    --purple-light:#4d2a80;
    --orange:#f39c1f;
    --grey-line:#8a8790;
    --white:#ffffff;
    --photo-bg:#e9ebee;
    --photo-suit:#8e96a6;
  }
  *{box-sizing:border-box;margin:0;padding:0}
  html,body{width:1200px;height:1200px;overflow:hidden}
  body{background:var(--bg);font-family:"Jost",sans-serif;position:relative}

  .card{position:absolute;left:250px;width:700px;height:400px;border-radius:26px;overflow:hidden;
        box-shadow:0 8px 22px rgba(0,0,0,.18)}

  /* Front card */
  .card-front{top:160px;background:linear-gradient(160deg,var(--purple-light) 0%,var(--purple) 45%,var(--purple-dark) 100%)}
  .card-front .photo{position:absolute;right:18px;top:18px;width:310px;height:300px;
        background:linear-gradient(180deg,var(--photo-bg) 0%,var(--photo-bg) 60%,var(--photo-suit) 100%)}
  .tagline{position:absolute;left:48px;top:150px;color:var(--white);font-weight:400;
        font-size:36px;line-height:40px;letter-spacing:.5px}
  .tagline .accent{color:var(--orange)}
  .card-front .brand{position:absolute;left:48px;top:292px}

  .brand{color:var(--white);font-family:"Jost",sans-serif;font-weight:400;font-size:64px;line-height:1;letter-spacing:-1px}

  /* Back card */
  .card-back{top:640px;background:linear-gradient(170deg,var(--purple-light) 0%,var(--purple) 50%,var(--purple-dark) 100%)}
  .card-back .wave{position:absolute;inset:0}
  .person{position:absolute;right:44px;top:26px;text-align:right}
  .person .name{font-weight:700;font-size:24px;color:var(--purple-dark)}
  .person .role{font-family:"Roboto",sans-serif;font-size:14px;color:var(--purple-dark);margin-top:2px}

  .contact-list{position:absolute;left:64px;top:200px;list-style:none;font-family:"Roboto",sans-serif;
        color:var(--white);font-size:17px}
  .contact-list li{display:flex;align-items:center;gap:12px;height:26px}
  .contact-list svg{width:16px;height:16px;flex:none}
  .card-back .brand{position:absolute;left:64px;top:290px;font-size:76px}

  .side-info{position:absolute;right:44px;top:222px;font-family:"Roboto",sans-serif;font-size:16px;color:var(--white);text-align:right}
  .find-us{display:flex;align-items:center;justify-content:flex-end;gap:6px}
  .find-us .social{width:18px;height:18px;border-radius:3px;background:var(--orange)}
  .find-us span{margin-right:4px}
  .abn{margin-top:10px}
  .abn .label{color:var(--orange)}
</style>
</head>
<body>

  <section class="card card-front" aria-label="Business card front">
    <div class="photo" role="img" aria-label="Head shot photo of the director in a suit and tie"></div>
    <p class="tagline">Let us<br>show you<br><span class="accent">property</span></p>
    <div class="brand">calvanto</div>
  </section>

  <section class="card card-back" aria-label="Business card back">
    <svg class="wave" viewBox="0 0 700 400" preserveAspectRatio="none" aria-hidden="true">
      <path d="M0,0 H700 V92 C600,100 520,110 430,125 C320,142 180,135 80,150 C40,156 15,168 0,180 Z" fill="var(--orange)"/>
      <path d="M0,195 C30,178 60,168 110,162 C220,150 330,158 440,140 C540,124 620,112 700,110"
            fill="none" stroke="var(--grey-line)" stroke-width="10"/>
    </svg>

    <div class="person">
      <div class="name">Daniel Tran</div>
      <div class="role">Director</div>
    </div>

    <ul class="contact-list">
      <li>
        <svg viewBox="0 0 16 16" aria-hidden="true"><rect width="16" height="16" rx="2" fill="var(--orange)"/><rect x="5" y="3" width="6" height="10" rx="1" fill="none" stroke="var(--purple)" stroke-width="1.4"/></svg>
        0400 555 123
      </li>
      <li>
        <svg viewBox="0 0 16 16" aria-hidden="true"><circle cx="8" cy="8" r="7" fill="var(--orange)"/><path d="M1,8 H15 M8,1 C4,5 4,11 8,15 M8,1 C12,5 12,11 8,15" fill="none" stroke="var(--purple)" stroke-width="1"/></svg>
        www.calvanto.com.au
      </li>
      <li>
        <svg viewBox="0 0 16 16" aria-hidden="true"><rect x="1" y="3" width="14" height="10" rx="1" fill="var(--orange)"/><path d="M1,3 L8,9 L15,3" fill="none" stroke="var(--purple)" stroke-width="1.2"/></svg>
        daniel.tran@calvanto.com.au
      </li>
    </ul>

    <div class="brand">calvanto</div>

    <div class="side-info">
      <div class="find-us"><span>Find us:</span><i class="social"></i><i class="social"></i><i class="social"></i></div>
      <div class="abn"><span class="label">ABN:</span> 12 345 678 901</div>
    </div>
  </section>

</body>
</html>
```